LinkedIn Banner Design for B2B Consulting Firm

Take the already developed logo (attached) and incorporate it into a creative banner design for placement on LinkedIn (the social media platform targeting business users). The banner will be used on the firm's company profile page on LinkedIn (not yet created).

```html
<!DOCTYPE html>
<html lang="en">
<head>
<meta charset="utf-8">
<title>Fractional Marketing Services Banner</title>
<link rel="stylesheet" href="https://fonts.googleapis.com/css2?family=Lora:wght@400;700&display=swap">
<style>
  :root {
    --canvas-bg: #d5d5d5;
    --olive: #50644f;
    --olive-light: #c9cfc6;
    --white: #ffffff;
    --wood: #8a5a36;
    --wood-light: #c9a27a;
  }
  html, body {
    margin: 0;
    padding: 0;
    width: 1200px;
    height: 799px;
    overflow: hidden;
    background: var(--canvas-bg);
  }
  .banner {
    position: absolute;
    left: 50px;
    top: 306px;
    width: 1100px;
    height: 186px;
    background: var(--olive);
    overflow: hidden;
  }
  .banner-decor {
    position: absolute;
    inset: 0;
    width: 1100px;
    height: 186px;
  }
  .headline-rule {
    position: absolute;
    left: 221px;
    top: 48px;
    width: 4px;
    height: 89px;
    background: var(--white);
  }
  .headline {
    position: absolute;
    left: 247px;
    top: 36px;
    margin: 0;
    color: var(--white);
    font-family: "Lora", Georgia, serif;
  }
  .headline-title {
    display: block;
    font-weight: 700;
    font-size: 35px;
    line-height: 40px;
    letter-spacing: -0.2px;
  }
  .headline-audience {
    display: block;
    font-weight: 400;
    font-size: 28px;
    line-height: 33px;
    margin-top: 1px;
  }
</style>
</head>
<body>
  <section class="banner">
    <svg class="banner-decor" viewBox="0 0 1100 186" xmlns="http://www.w3.org/2000/svg">
      <defs>
        <linearGradient id="sheenGradient" x1="0" y1="0" x2="1" y2="0">
          <stop offset="0" stop-color="#50644f"/>
          <stop offset="1" stop-color="#c9cfc6"/>
        </linearGradient>
        <linearGradient id="cornerGradient" x1="0" y1="0" x2="1" y2="0">
          <stop offset="0" stop-color="#e4e7e2"/>
          <stop offset="1" stop-color="#8f9c8c"/>
        </linearGradient>
        <linearGradient id="photoGradient" x1="0" y1="0" x2="1" y2="1">
          <stop offset="0" stop-color="#6b4a30"/>
          <stop offset="0.5" stop-color="#a87a52"/>
          <stop offset="1" stop-color="#d9cfc4"/>
        </linearGradient>
      </defs>
      <path class="sheen-band" d="M795 0 L880 94 Q893 108 906 94 L1002 0 Z" fill="url(#sheenGradient)"/>
      <path class="corner-accent" d="M1049 0 L1100 52 L1100 0 Z" fill="url(#cornerGradient)"/>
      <g class="photo-frame" transform="translate(1032 150) rotate(45)">
        <rect x="-101" y="-101" width="202" height="202" rx="18" fill="var(--white)"/>
        <rect x="-96" y="-96" width="192" height="192" rx="15" fill="url(#photoGradient)"
              role="img" aria-label="Photo: team working at a desk with laptop, coffee and charts"/>
      </g>
    </svg>
    <div class="headline-rule"></div>
    <h1 class="headline">
      <span class="headline-title">Fractional Marketing Services</span>
      <span class="headline-audience">For Private Equity Firms, Family Offices</span>
      <span class="headline-audience">&amp; Investment Banks</span>
    </h1>
  </section>
</body>
</html>
```